Heron Loan Partners Business Card

We need a business card design for our mortgage servicing company. In addition to servicing the loans of homeowners, we help homeowners with purchasing their homes and any mortgage refinancing. We would like to see designs that use the colors in the logo attached below (gold-ish yellow and navy blue), and any other design you deem fit! The design should communicate a simpler life with smart mortgages provided by Heron.

```html
<!DOCTYPE html>
<html lang="en">
<head>
<meta charset="utf-8">
<title>Heron Loan Partners Business Card</title>
<link href="https://fonts.googleapis.com/css2?family=Libre+Baskerville:wght@400;700&display=swap" rel="stylesheet">
<style>
  :root {
    --backdrop: #b3b3b3;
    --card-gold: #dfb13f;
    --navy: #27235a;
    --ink: #1e1a14;
    --rule: #15120d;
  }
  * { margin: 0; padding: 0; box-sizing: border-box; }
  html, body {
    width: 1154px; height: 1200px; overflow: hidden;
    background: var(--backdrop);
    font-family: "Libre Baskerville", Georgia, serif;
  }
  .canvas { position: relative; width: 1154px; height: 1200px; }
  .card {
    position: absolute; left: 191px; width: 771px;
    background: var(--card-gold);
    border-radius: 38px;
    box-shadow: 0 7px 9px rgba(0,0,0,0.18);
  }
  .card--front { top: 138px; height: 440px; }
  .card--back { top: 620px; height: 442px; width: 773px; }

  .brand-name {
    position: absolute;
    color: var(--navy);
    font-weight: 700;
    white-space: nowrap;
    display: flex; align-items: center; gap: 12px;
  }
  .brand-dot { width: 14px; height: 14px; border-radius: 50%; background: var(--navy); flex: none; }
  .card--front .brand-name { left: 0; right: 0; top: 200px; justify-content: center; font-size: 36px; }
  .card--back .brand-name { right: 48px; top: 80px; font-size: 26px; }

  .holder { position: absolute; left: 46px; top: 252px; }
  .holder-name { font-size: 26px; font-weight: 700; color: var(--navy); letter-spacing: 0.3px; line-height: 1; }
  .holder-title { margin-top: 12px; font-size: 16px; color: var(--ink); line-height: 1; }

  .divider { position: absolute; left: 46px; top: 322px; width: 681px; height: 2px; background: var(--rule); }

  .contacts { position: absolute; left: 46px; top: 340px; list-style: none; }
  .contacts li {
    display: flex; align-items: center; gap: 11px;
    height: 30px; font-size: 16px; color: var(--ink);
  }
  .contacts svg { width: 19px; height: 19px; fill: var(--navy); flex: none; }

  .address {
    position: absolute; right: 46px; top: 361px;
    text-align: right; font-size: 16px; line-height: 25px; color: var(--ink);
    font-style: normal;
  }
</style>
</head>
<body>
<main class="canvas">
  <section class="card card--front" aria-label="Card front">
    <div class="brand-name"><span class="brand-dot"></span>Heron Loan Partners</div>
  </section>

  <section class="card card--back" aria-label="Card back">
    <div class="brand-name"><span class="brand-dot"></span>Heron Loan Partners</div>

    <div class="holder">
      <h1 class="holder-name">DANIEL FOSTER</h1>
      <p class="holder-title">MANAGING DIRECTOR</p>
    </div>

    <div class="divider"></div>

    <ul class="contacts">
      <li>
        <svg viewBox="0 0 24 24" aria-hidden="true"><path d="M6.6 10.8a15.1 15.1 0 0 0 6.6 6.6l2.2-2.2a1 1 0 0 1 1-.25 11.4 11.4 0 0 0 3.6.57 1 1 0 0 1 1 1V20a1 1 0 0 1-1 1A17 17 0 0 1 3 4a1 1 0 0 1 1-1h3.5a1 1 0 0 1 1 1c0 1.25.2 2.45.57 3.57a1 1 0 0 1-.25 1z"/></svg>
        044-987 654 321
      </li>
      <li>
        <svg viewBox="0 0 24 24" aria-hidden="true"><path d="M2 5h20v14H2z M3.5 6.5 12 12.5l8.5-6" fill="none" stroke="#27235a" stroke-width="0"/><path d="M2 5h20v14H2zm2 2v.4l8 5.6 8-5.6V7l-8 5.6z"/></svg>
        info@heronloans.com
      </li>
      <li>
        <svg viewBox="0 0 24 24" aria-hidden="true"><path d="M12 2a10 10 0 1 0 0 20 10 10 0 0 0 0-20zm6.9 6h-3a15.6 15.6 0 0 0-1.4-3.6A8 8 0 0 1 18.9 8zM12 4a14 14 0 0 1 1.9 4h-3.8A14 14 0 0 1 12 4zM4.3 14a8.2 8.2 0 0 1 0-4h3.4a16.5 16.5 0 0 0 0 4zm.8 2h3a15.6 15.6 0 0 0 1.4 3.6A8 8 0 0 1 5.1 16zm3-8h-3a8 8 0 0 1 4.4-3.6A15.6 15.6 0 0 0 8.1 8zM12 20a14 14 0 0 1-1.9-4h3.8A14 14 0 0 1 12 20zm2.3-6H9.7a14.7 14.7 0 0 1 0-4h4.6a14.7 14.7 0 0 1 0 4zm.2 5.6a15.6 15.6 0 0 0 1.4-3.6h3a8 8 0 0 1-4.4 3.6zm1.8-5.6a16.5 16.5 0 0 0 0-4h3.4a8.2 8.2 0 0 1 0 4z"/></svg>
        www.heronloanpartners.com
      </li>
    </ul>

    <address class="address">
      421, Address line goes here<br>
      45452, Country name
    </address>
  </section>
</main>
</body>
</html>
```